Anzeigengestaltung für Fliesenlegermeister
Zielgruppe
Ich bin ein Fliesenlegermeister und möchte mich selbstständig machen, ich saniere Bäder, Böden mit Fliesen, Fliesenspiegel und ich möchte eine Anzeige in den regionalen Zeitungen machen. Ich spreche alle Altersklassen mit Bädern für Sanierungen, Bodenfliesen und Neubauten an. Reparatur und Silikonarbeiten sowie Trockenbauarbeiten am eigenen Heim .
Aufgabenstellung
Ich möchte gern meine Kontaktdaten und die Farben vom Logo wieder finden,
als Beispiel habe ich meine aktuelle Visitenkarte beigefügt Dort finden sich die Kontaktdaten. Meine Arbeiten sind insbesondere :
Fliesenverlegung
Badsanierung
barrierefreie Bäder
Reparaturarbeiten
Silikonarbeiten
Trockenbau
Ob nun genau alle 6 Punkte in der Anzeige angezeigt werden soll bin ich mir nicht sicher oder ob nur 4 Beschreibungen reichen, damit es nicht zu viel wird.

```html
<!DOCTYPE html>
<html lang="de">
<head>
<meta charset="utf-8">
<title>Jonas Wendrak – Fliesenlegermeister</title>
<link rel="stylesheet" href="https://fonts.googleapis.com/css2?family=Arimo:wght@400;500;700&family=Montserrat:wght@500;600&display=swap">
<style>
  :root {
    --navy: #16335f;
    --navy-dark: #0f2546;
    --blue-deep: #1f4a82;
    --blue-mid: #35689f;
    --blue-light: #6d98c4;
    --white: #ffffff;
    --ink: #111418;
    --photo-gray: #6c6f72;
    --photo-light: #b9bbbd;
  }
  * { margin: 0; padding: 0; box-sizing: border-box; }
  html, body { width: 1200px; height: 857px; overflow: hidden; background: var(--white); }
  .ad {
    position: relative;
    width: 1200px;
    height: 857px;
    overflow: hidden;
    font-family: "Arimo", Arial, sans-serif;
    color: var(--white);
  }
  .backdrop {
    position: absolute; inset: 0;
    background:
      radial-gradient(ellipse at 75% 25%, rgba(160,195,230,0.45), transparent 55%),
      linear-gradient(120deg, var(--blue-deep) 0%, var(--blue-mid) 45%, var(--blue-light) 75%, var(--blue-mid) 100%);
  }
  .shapes { position: absolute; inset: 0; }
  .brand {
    position: absolute; left: 30px; top: 66px;
    display: flex; align-items: center; gap: 22px;
    color: var(--navy);
    font-family: "Montserrat", Arial, sans-serif;
    font-weight: 600;
  }
  .brand-mark { width: 62px; height: 62px; background: var(--navy); }
  .brand-name { font-size: 35px; letter-spacing: 1px; line-height: 1; }
  .brand-title {
    font-size: 19px; letter-spacing: 1.5px; margin-top: 8px;
    border-left: 3px solid var(--navy); padding-left: 8px; margin-left: -12px;
  }
  .headline { position: absolute; left: 684px; top: 118px; }
  .headline-kicker { font-size: 41px; font-weight: 700; letter-spacing: 0.3px; line-height: 1.1; }
  .headline-main { font-size: 88px; font-weight: 700; line-height: 1; margin-top: 6px; letter-spacing: 0.5px; }
  .services { position: absolute; left: 690px; top: 288px; list-style: none; }
  .services li {
    display: flex; align-items: center; gap: 12px;
    font-size: 33px; font-weight: 500; height: 65px;
  }
  .services svg { width: 26px; height: 26px; flex: none; }
  .photo {
    position: absolute; left: 60px; top: 308px; width: 588px; height: 442px;
    background: linear-gradient(180deg, var(--photo-gray) 0%, #8a8c8e 55%, var(--photo-light) 100%);
  }
  .contact-left {
    position: absolute; left: 30px; top: 771px; height: 86px;
    display: flex; align-items: center; font-size: 21px; line-height: 1.3;
  }
  .contact-left .item { display: flex; align-items: center; gap: 14px; }
  .contact-left .divider { width: 3px; height: 58px; background: var(--white); margin: 0 18px 0 22px; }
  .contact-left svg { width: 30px; height: 30px; flex: none; }
  .contact-phone {
    position: absolute; left: 742px; top: 746px; height: 108px;
    display: flex; align-items: center; gap: 22px; color: var(--ink);
  }
  .contact-phone .numbers { font-size: 37px; font-weight: 700; line-height: 1.25; }
  .contact-phone svg { width: 44px; height: 44px; }
</style>
</head>
<body>
<div class="ad">
  <div class="backdrop" role="img" aria-label="Hintergrundfoto eines modernen Badezimmers in Blautönen"></div>

  <svg class="shapes" width="1200" height="857" viewBox="0 0 1200 857">
    <polygon points="610,0 660,0 430,228 0,228 0,212 386,212" fill="var(--navy)"/>
    <polygon points="0,0 610,0 386,212 0,212" fill="var(--white)"/>
    <rect x="0" y="771" width="1200" height="86" fill="var(--navy-dark)"/>
    <polygon points="762,738 1200,738 1200,857 724,857" fill="var(--white)"/>
  </svg>

  <div class="brand">
    <div class="brand-mark"></div>
    <div>
      <div class="brand-name">JONAS WENDRAK</div>
      <div class="brand-title">FLIESENLEGERMEISTER</div>
    </div>
  </div>

  <div class="headline">
    <div class="headline-kicker">Fliesenlegermeister</div>
    <div class="headline-main">Spezialistin</div>
  </div>

  <ul class="services">
    <li><svg viewBox="0 0 24 24"><path d="M3 13l6 6L21 6" fill="none" stroke="#fff" stroke-width="3.5" stroke-linecap="round" stroke-linejoin="round"/></svg>Fliesenverlegung</li>
    <li><svg viewBox="0 0 24 24"><path d="M3 13l6 6L21 6" fill="none" stroke="#fff" stroke-width="3.5" stroke-linecap="round" stroke-linejoin="round"/></svg>Badsanierung</li>
    <li><svg viewBox="0 0 24 24"><path d="M3 13l6 6L21 6" fill="none" stroke="#fff" stroke-width="3.5" stroke-linecap="round" stroke-linejoin="round"/></svg>Barrierefreie Bäder</li>
    <li><svg viewBox="0 0 24 24"><path d="M3 13l6 6L21 6" fill="none" stroke="#fff" stroke-width="3.5" stroke-linecap="round" stroke-linejoin="round"/></svg>Reparaturarbeiten</li>
    <li><svg viewBox="0 0 24 24"><path d="M3 13l6 6L21 6" fill="none" stroke="#fff" stroke-width="3.5" stroke-linecap="round" stroke-linejoin="round"/></svg>Silikonarbeiten</li>
    <li><svg viewBox="0 0 24 24"><path d="M3 13l6 6L21 6" fill="none" stroke="#fff" stroke-width="3.5" stroke-linecap="round" stroke-linejoin="round"/></svg>Trockenbau</li>
  </ul>

  <div class="photo" role="img" aria-label="Foto eines gefliesten Badezimmers mit Spiegel, Waschtisch, WC und Dusche"></div>

  <div class="contact-left">
    <div class="item">
      <svg viewBox="0 0 24 24"><path d="M12 2a7 7 0 0 0-7 7c0 5 7 13 7 13s7-8 7-13a7 7 0 0 0-7-7zm0 9.5A2.5 2.5 0 1 1 12 6.5a2.5 2.5 0 0 1 0 5z" fill="#fff"/></svg>
      <div>Lindenweg 7,<br>38100 Musterstadt</div>
    </div>
    <div class="divider"></div>
    <div class="item">
      <svg viewBox="0 0 24 24"><rect x="2" y="5" width="20" height="14" rx="2" fill="#fff"/><path d="M3 6l9 7 9-7" fill="none" stroke="var(--navy-dark)" stroke-width="1.8"/></svg>
      <div>info@fliesenlegermeister-wendrak.de</div>
    </div>
  </div>

  <div class="contact-phone">
    <svg viewBox="0 0 24 24"><path d="M6.6 10.8a15 15 0 0 0 6.6 6.6l2.2-2.2a1 1 0 0 1 1-.25 11.4 11.4 0 0 0 3.6.57 1 1 0 0 1 1 1V20a1 1 0 0 1-1 1A17 17 0 0 1 3 4a1 1 0 0 1 1-1h3.5a1 1 0 0 1 1 1c0 1.25.2 2.45.57 3.6a1 1 0 0 1-.25 1z" fill="var(--ink)"/></svg>
    <div class="numbers">05301/4471920<br>Mobil 01719926354</div>
  </div>
</div>
</body>
</html>
```